Application page web design and internal pages

Create a web site where home
Page looks like an application screen for a mobile phone

Use bold icons and colors with images that have round edges

PorlenPurse Apps is name of page

Search bar at the top

Use colors from Vextaro.org for background

Price of ZORBS in top right corner (https://www.quelvix.example/trade/en-US?symbol=ZORBS_USDT&layout=basic&theme=dark)

Pages within each app should be the same color as the icon

Use the following as app icons on the page:
Key
Icon name: first screen; second screen (text)

⁃ Balances: enter pin; display balances (Your account can hold multiple currency denominations. Your balances are: ZORBS 1234567890)
⁃ Transactions: enter pin; display transactions (Your last 5 payments are ZORBS 10 from Vextaro)
⁃ Send Money: enter phone number, enter amount, send button; display message
⁃ Create Account: choose country code, enter phone number, create button; enter pin; display message ( (phone number) will be notified when their account has been created)
⁃ My Wallet Address: enter pin; display public key (IMPORTANT Send only STELLAR blockchain tokens to this deposit address: GDXQ7PLM2ZNVA9TRK4WSEY8HCBUJ6FOGDLIXP3QM5RTVKNAWZEHOBCYS)
⁃ Private Message: enter phone number, enter message, choose image, send button; enter pin; display message ( (phone number) will be notified when their message has been created)
⁃ Buy Cryptocurrency: drop drown menu of cryptocurrency to purchase (Bitcoin/Ethereum/Stellar/ZORBS), Amount in USD field, amount in chosen cryptocurrency displayed, frequency drop down menu (once/daily/weekly/monthly), buy button; enter card information (name, card number, expiration date, cvv, billing address, zip code), confirm buy button, transactions will appear on your billing statement as VEXTARO; enter pin screen; display message (You will be notified when your coin is received)
⁃ NFTs: upload image, title, description, link media, create NFT button; enter pin screen; display message (You will be notified when your NFT is created)
⁃ Earn: display message (Earn cryptocurrency doing what you do everyday, coming soon)
⁃ Files/Vault: display message (Storage for your photos, documents and more, coming soon)
⁃ Wealth: display message (Build wealth by working with a financial professional to get you to the next level), check box (I would like a financial professional to contact me about building wealth), contact me button; display message (A financial professional will contact you to achieve your financial goals)
⁃ Education: display message (Learn more about everything, coming soon)
⁃ News: display message (News from around the world, coming soon)
⁃ FAQs: use FAQs from this link https://vextaro.example/faq
⁃ Contact Us: enter message, send button; display message (Thank you for reaching out. We will reply to your message in the order it was received. Your patience is appreciated. Blessings.)

Requirements
Must have
• Application home page that looks like the Home Screen of a mobile phone
Nice to have
• Colorful icons

```html
<!DOCTYPE html>
<html lang="en">
<head>
<meta charset="utf-8">
<title>PorlenPurse App</title>
<link rel="stylesheet" href="https://fonts.googleapis.com/css2?family=Lato:wght@700;900&family=Montserrat:wght@700&display=swap">
<style>
  :root {
    --navy-deep: #0b0d35;
    --navy: #151a6e;
    --blue-glow: #2a2fb0;
    --bar: rgba(12, 14, 48, 0.82);
    --cyan: #34d6e8;
    --white: #ffffff;
  }
  * { box-sizing: border-box; margin: 0; padding: 0; }
  html, body { width: 796px; height: 1200px; overflow: hidden; }
  body {
    font-family: "Lato", sans-serif;
    background:
      radial-gradient(ellipse 70% 45% at 85% 25%, rgba(60, 70, 210, 0.45), transparent 70%),
      radial-gradient(ellipse 60% 40% at 15% 80%, rgba(50, 55, 190, 0.4), transparent 70%),
      linear-gradient(160deg, var(--navy) 0%, var(--navy-deep) 55%, var(--navy) 100%);
    color: var(--white);
  }
  .app { position: relative; width: 796px; height: 1200px; }
  .top-space { height: 137px; }
  .app-bar {
    height: 80px;
    background: var(--bar);
    display: flex;
    align-items: center;
    padding: 0 32px;
  }
  .app-title {
    font-family: "Lato", sans-serif;
    font-weight: 900;
    font-size: 31px;
    color: var(--cyan);
    flex: 1;
  }
  .price {
    font-family: "Montserrat", sans-serif;
    font-weight: 700;
    font-size: 24px;
    display: flex;
    align-items: center;
    gap: 10px;
    margin-right: 38px;
  }
  .bar-icon { width: 30px; height: 30px; margin-left: 28px; }
  .home-grid {
    display: grid;
    grid-template-columns: repeat(3, 1fr);
    grid-auto-rows: 152px;
    padding: 58px 24px 0;
  }
  .app-tile {
    display: flex;
    flex-direction: column;
    align-items: center;
    text-decoration: none;
  }
  .app-icon {
    width: 82px;
    height: 82px;
    border-radius: 22px;
  }
  .app-label {
    margin-top: 14px;
    font-weight: 700;
    font-size: 20px;
    color: var(--cyan);
    white-space: nowrap;
  }
  .i-balances { background: linear-gradient(135deg, #f2a25a, #a0643a); }
  .i-transactions { background: linear-gradient(135deg, #a978e8, #27c08a); }
  .i-send { background: linear-gradient(135deg, #3fae4a, #f5c23a); }
  .i-create { background: linear-gradient(135deg, #f25a7a, #2fd07a); }
  .i-wallet { background: linear-gradient(135deg, #1f8a9a, #f2b53a); }
  .i-message { background: linear-gradient(135deg, #7a6cf0, #3a8af0); }
  .i-buy { background: linear-gradient(135deg, #f0a02a, #3a8af0); }
  .i-nft { background: linear-gradient(135deg, #3ad0f0, #1a3a9a); }
  .i-earn { background: linear-gradient(135deg, #f7d04a, #e59a1a); }
  .i-vault { background: linear-gradient(135deg, #3a9af0, #1a5ab0); }
  .i-wealth { background: linear-gradient(135deg, #f5c23a, #3a3a4a); }
  .i-education { background: linear-gradient(135deg, #f0f0f0, #e0453a); }
  .i-news { background: linear-gradient(135deg, #6ab0f0, #2a6ad0); }
  .i-faq { background: linear-gradient(135deg, #5ab8f0, #f04a8a); }
  .i-contact { background: linear-gradient(135deg, #f7d04a, #2a3a7a); }
</style>
</head>
<body>
<main class="app">
  <div class="top-space"></div>
  <header class="app-bar">
    <h1 class="app-title">PorlenPurse App</h1>
    <div class="price">Zorbs 1.75
      <svg width="12" height="8" viewBox="0 0 12 8"><path d="M1 1l5 5 5-5z" fill="#fff"/></svg>
    </div>
    <svg class="bar-icon" viewBox="0 0 24 24" aria-label="Search"><circle cx="10" cy="10" r="6.5" fill="none" stroke="#fff" stroke-width="2.4"/><path d="M15 15l6 6" stroke="#fff" stroke-width="2.6" stroke-linecap="round"/></svg>
    <svg class="bar-icon" viewBox="0 0 24 24" aria-label="Profile"><circle cx="12" cy="7.5" r="5" fill="#fff"/><path d="M2.5 23c0-6 4.3-9 9.5-9s9.5 3 9.5 9z" fill="#fff"/></svg>
  </header>

  <nav class="home-grid">
    <a class="app-tile" href="#"><div class="app-icon i-balances" role="img" aria-label="Wallet with banknotes icon"></div><span class="app-label">Balances</span></a>
    <a class="app-tile" href="#"><div class="app-icon i-transactions" role="img" aria-label="Phone with payment receipt icon"></div><span class="app-label">Transactions</span></a>
    <a class="app-tile" href="#"><div class="app-icon i-send" role="img" aria-label="Envelope with money icon"></div><span class="app-label">Send Money</span></a>

    <a class="app-tile" href="#"><div class="app-icon i-create" role="img" aria-label="New user account icon"></div><span class="app-label">Create Account</span></a>
    <a class="app-tile" href="#"><div class="app-icon i-wallet" role="img" aria-label="Crypto wallet icon"></div><span class="app-label">My Wallet Address</span></a>
    <a class="app-tile" href="#"><div class="app-icon i-message" role="img" aria-label="Locked chat bubbles icon"></div><span class="app-label">Private Message</span></a>

    <a class="app-tile" href="#"><div class="app-icon i-buy" role="img" aria-label="Shopping basket with coin icon"></div><span class="app-label">Buy Cryptocurrency</span></a>
    <a class="app-tile" href="#"><div class="app-icon i-nft" role="img" aria-label="NFT hexagon badge icon"></div><span class="app-label">NFTs</span></a>
    <a class="app-tile" href="#"><div class="app-icon i-earn" role="img" aria-label="Stack of gold coins icon"></div><span class="app-label">Earn</span></a>

    <a class="app-tile" href="#"><div class="app-icon i-vault" role="img" aria-label="Safe vault icon"></div><span class="app-label">Files/Vault</span></a>
    <a class="app-tile" href="#"><div class="app-icon i-wealth" role="img" aria-label="Money bag with coins icon"></div><span class="app-label">Wealth</span></a>
    <a class="app-tile" href="#"><div class="app-icon i-education" role="img" aria-label="Open book with pencil icon"></div><span class="app-label">Education</span></a>

    <a class="app-tile" href="#"><div class="app-icon i-news" role="img" aria-label="News screen icon"></div><span class="app-label">News</span></a>
    <a class="app-tile" href="#"><div class="app-icon i-faq" role="img" aria-label="Question speech bubbles icon"></div><span class="app-label">FAQ</span></a>
    <a class="app-tile" href="#"><div class="app-icon i-contact" role="img" aria-label="Support agent icon"></div><span class="app-label">Contact Us</span></a>
  </nav>
</main>
</body>
</html>
```